Business card design Needed for new logo / Construction business, home extensions and new builds

We need a business card design using our new logo files which i will attach to this project :)

We are a small construction business specialising in home extensions, new builds and property development. We are very ambitious and would appreciate professional and elegant designs for our new business card.

Very serious about using the services on MakerQuarry and recently acquired our new logo from here :)

Please get involved, i will feedback when i can as i am very busy but can respond daily, thanks

Target Market(s)

People that want to build onto their houses, new building developments or adding too their existing property

Industry/Entity Type

Construction

Contact Information for Business Card

Renwick Tolliver Construction, Lionel Ashby (Managing Director), Tel 07822254961, email - info@renwick-tolliver, www.renwick-tolliver.co.uk

Colors

Designer to choose colors to be used in the design.

Requirements
Must have
• I like a deep grey on the back please. A lot of you have provided black from and back, try mixing things up a little. The black looks cool 😎 Thanks

```html
<!DOCTYPE html>
<html lang="en">
<head>
<meta charset="utf-8">
<title>Renwick Tolliver Construction – Business Card</title>
<link href="https://fonts.googleapis.com/css2?family=Marcellus&display=swap" rel="stylesheet">
<style>
  :root {
    --stage: #d9d6d2;
    --card-black: #0b0b0b;
    --pattern-deep: #15171b;
    --pattern-mid: #1f232a;
    --orange: #f7941d;
    --orange-bright: #ffb11f;
    --silver: #e6e6e6;
    --silver-dark: #9c9c9c;
    --text-light: #f2f2f2;
    --text-muted: #bdbdbd;
    --ghost: #1c2027;
  }
  * { box-sizing: border-box; margin: 0; padding: 0; }
  html, body { width: 1200px; height: 961px; overflow: hidden; }
  body {
    background: var(--stage);
    font-family: "Marcellus", Georgia, serif;
    position: relative;
  }
  .card {
    position: absolute;
    width: 620px;
    height: 354px;
    background: var(--card-black);
    overflow: hidden;
    box-shadow: 0 10px 28px rgba(0,0,0,.35);
  }
  .card--contact { left: 520px; top: 90px; }
  .card--brand { left: 60px; top: 520px; }

  .card__bands { position: absolute; inset: 0; width: 100%; height: 100%; }

  /* contact side */
  .brand-line {
    position: absolute; left: 38px; top: 30px;
    display: flex; align-items: center; gap: 12px;
  }
  .brand-line__square { width: 22px; height: 22px; background: var(--orange); }
  .brand-line__name {
    color: var(--silver); font-size: 21px; letter-spacing: 1.5px; text-transform: uppercase;
  }
  .ghost-name {
    position: absolute; right: 26px; top: 130px; width: 280px;
    color: var(--ghost); font-size: 34px; line-height: 1.15; text-align: right;
    text-transform: uppercase; letter-spacing: 2px;
  }
  .contact-list { position: absolute; left: 38px; top: 86px; list-style: none; }
  .contact-list li {
    display: flex; align-items: center; gap: 12px;
    color: var(--text-light); font-size: 19px; height: 32px;
  }
  .contact-list li.person { height: 50px; margin-bottom: 4px; }
  .icon {
    width: 24px; height: 24px; border-radius: 50%; background: var(--orange);
    display: flex; align-items: center; justify-content: center; flex: none;
  }
  .icon svg { width: 14px; height: 14px; }
  .person__name { font-size: 22px; line-height: 1; }
  .person__role { font-size: 13px; color: var(--text-muted); display: block; margin-top: 3px; }

  /* brand side */
  .pattern-field {
    position: absolute; inset: 0;
    background: linear-gradient(135deg, var(--pattern-mid), var(--pattern-deep) 60%, #0c0d10);
  }
  .brand-center {
    position: absolute; left: 120px; right: 40px; top: 130px;
    display: flex; align-items: center; justify-content: center; gap: 14px;
  }
  .brand-center__square { width: 26px; height: 26px; background: var(--orange); flex: none; }
  .brand-center__name {
    color: var(--silver); font-size: 30px; letter-spacing: 2px; text-transform: uppercase;
    line-height: 1.2;
  }
</style>
</head>
<body>

  <section class="card card--contact" aria-label="Card contact side">
    <svg class="card__bands" viewBox="0 0 620 354" preserveAspectRatio="none" aria-hidden="true">
      <path d="M0,262 L400,304 C440,308 470,296 510,292 L620,290 L620,300 L510,302 C470,306 440,318 400,316 L0,280 Z" fill="var(--silver)"/>
      <path d="M0,284 L390,322 C430,326 460,314 500,310 L620,308 L620,354 L0,354 Z" fill="var(--orange)"/>
      <path d="M0,300 L380,338 L620,340 L620,354 L0,354 Z" fill="var(--orange-bright)"/>
    </svg>

    <div class="brand-line">
      <span class="brand-line__square"></span>
      <span class="brand-line__name">Renwick Tolliver Construction</span>
    </div>

    <div class="ghost-name" aria-hidden="true">Renwick Tolliver Construction</div>

    <ul class="contact-list">
      <li class="person">
        <span class="icon"><svg viewBox="0 0 14 14"><circle cx="7" cy="4.5" r="3" fill="#fff"/><path d="M1.5,13 C1.5,9 12.5,9 12.5,13 Z" fill="#fff"/></svg></span>
        <span><span class="person__name">Lionel Ashby</span><span class="person__role">Managing Director</span></span>
      </li>
      <li>
        <span class="icon"><svg viewBox="0 0 14 14"><path d="M3,1.5 L5,1.5 L6,4.5 L4.5,5.6 C5.3,7.4 6.6,8.7 8.4,9.5 L9.5,8 L12.5,9 L12.5,11 C12.5,12 11.5,12.6 10.5,12.5 C5.8,12 2,8.2 1.5,3.5 C1.4,2.5 2,1.5 3,1.5 Z" fill="#fff"/></svg></span>
        07822254961
      </li>
      <li>
        <span class="icon"><svg viewBox="0 0 14 14"><rect x="1.5" y="3" width="11" height="8" fill="none" stroke="#fff" stroke-width="1.3"/><path d="M1.5,3 L7,8 L12.5,3" fill="none" stroke="#fff" stroke-width="1.3"/></svg></span>
        info@renwick-tolliver
      </li>
      <li>
        <span class="icon"><svg viewBox="0 0 14 14"><circle cx="7" cy="7" r="5.5" fill="none" stroke="#fff" stroke-width="1.2"/><ellipse cx="7" cy="7" rx="2.4" ry="5.5" fill="none" stroke="#fff" stroke-width="1.1"/><path d="M1.5,7 H12.5" stroke="#fff" stroke-width="1.1"/></svg></span>
        www.renwick-tolliver.co.uk
      </li>
      <li>
        <span class="icon"><svg viewBox="0 0 14 14"><path d="M7,1.5 L13,7 L11,7 L11,12.5 L8.3,12.5 L8.3,9 L5.7,9 L5.7,12.5 L3,12.5 L3,7 L1,7 Z" fill="#fff"/></svg></span>
        Renwick Tolliver Construction
      </li>
    </ul>
  </section>

  <section class="card card--brand" aria-label="Card brand side">
    <div class="pattern-field" role="img" aria-label="Dark tonal repeat pattern background"></div>
    <svg class="card__bands" viewBox="0 0 620 354" preserveAspectRatio="none" aria-hidden="true">
      <path d="M0,0 L22,0 L90,250 C100,285 120,300 150,310 L160,354 L140,354 C110,330 90,310 78,280 L0,20 Z" fill="var(--silver)"/>
      <path d="M0,30 L70,280 C82,312 110,335 140,354 L0,354 Z" fill="var(--orange)"/>
      <path d="M0,110 L55,300 C66,325 80,342 96,354 L0,354 Z" fill="var(--orange-bright)"/>
    </svg>
    <div class="brand-center">
      <span class="brand-center__square"></span>
      <span class="brand-center__name">Renwick Tolliver<br>Construction</span>
    </div>
  </section>

</body>
</html>
```